RV7 - Rapid Vigil Field Operations Suite

I need an introductory website for RV7 which describes the features of the product and the ease of use of the product. The product is focused on Preparing for an incident using Volunteer and Resource management and then responding to an incident with Incident Management, Team Management, Task Management and Communication Management. Once a situation is handled, the application provides complete reporting on each of the above aspects

Target Market(s)

Local Government entities, specifically the emergency department directors or coordinators

Industry/Entity Type

Government Office

Coding

Coded - Design and coding required

Font styles to use
Sans Serif

Requirements
Must have
• Clear layout with modern images. I want to be able to get a clear understanding of the features of the product and the ease of use. I would like to high light how the application helps in Communication Management, Team Management, Task Management and Incident Managements. Also, how the use of application helps to get an immediate snap shot of how well an incident was handled. I want to highlight how the Dashboard provides a quick look at the Incident(s) being managed
Nice to have
• I would like to in the future add videos to the site. At this point don't have any ideas about nice to have features
Should not have
• traditional designs. I am looking for a slick, modern looking website. Clean design is the key.

```html
<!DOCTYPE html>
<html lang="en">
<head>
<meta charset="utf-8">
<title>RV7 - Rapid Vigil Field Operations Suite</title>
<link href="https://fonts.googleapis.com/css2?family=Open+Sans:wght@400;600;700;800&display=swap" rel="stylesheet">
<style>
:root{
  --blue:#1b4a9e;
  --blue-mid:#2c5cb4;
  --green:#8dc63f;
  --ink:#222;
  --dark:#2a2a2a;
  --darker:#1c1c1c;
  --card:#e9e9e9;
  --light:#e6e6e6;
  --white:#fff;
  --line:#d5def0;
  --alert:#e8a21a;
  --pin:#d9334f;
}
*{box-sizing:border-box;margin:0;padding:0}
html,body{width:1200px;height:2817px;overflow:hidden}
body{font-family:"Open Sans",Arial,sans-serif;color:var(--ink);background:var(--white);position:relative}
.section{position:absolute;left:0;width:1200px}
.btn{display:inline-block;background:var(--green);color:var(--white);font-weight:700;font-size:13px;text-transform:uppercase;text-align:center;border-radius:2px}

/* header */
.site-header{top:0;height:135px;background:var(--white)}
.brand{position:absolute;left:0;width:1200px;top:22px;display:flex;justify-content:center;align-items:center;gap:14px}
.brand-dot{width:58px;height:58px;border-radius:50%;background:var(--green)}
.brand-name{font-size:46px;font-weight:800;color:var(--blue);letter-spacing:1px}
.brand-tag{position:absolute;left:0;width:1200px;top:105px;text-align:center;font-size:12px;color:var(--blue)}
.login{position:absolute;right:88px;top:58px;font-size:12px;display:flex;align-items:center;gap:8px}

/* nav */
.main-nav{top:135px;height:53px;background:var(--green)}
.nav-list{position:absolute;left:86px;top:0;height:53px;display:flex;list-style:none}
.nav-list li{height:53px;line-height:53px;color:var(--white);font-weight:700;font-size:12px;padding:0 26px 0 0}
.nav-list li.active{background:var(--blue);padding:0 28px;margin-right:26px}
.search{position:absolute;left:965px;top:10px;width:149px;height:33px;display:flex}
.search-field{flex:1;background:var(--white);font-size:11px;color:#555;padding:9px 6px}
.search-btn{width:41px;background:#3a3a3a;display:flex;align-items:center;justify-content:center}

/* hero */
.hero{top:188px;height:623px;overflow:hidden}
.hero-photo{position:absolute;inset:0;background:
  radial-gradient(ellipse 260px 300px at 260px 330px,rgba(240,225,205,.55),transparent 70%),
  radial-gradient(ellipse 200px 260px at 600px 240px,rgba(235,205,160,.6),transparent 70%),
  radial-gradient(ellipse 300px 320px at 920px 260px,rgba(40,38,36,.55),transparent 70%),
  linear-gradient(100deg,#5f6a70 0%,#a9a39b 30%,#d4c2a9 52%,#7a7068 75%,#3d3936 100%)}
.hero-caption{position:absolute;left:494px;top:184px;width:620px;height:253px;background:rgba(25,25,25,.78);text-align:right;padding:86px 24px 0 0}
.hero-caption h1{font-size:48px;font-weight:700;color:var(--white);line-height:1}
.hero-caption p{font-size:13px;color:var(--white);margin-top:14px}
.hero-caption .btn{width:116px;height:40px;line-height:40px;margin-top:16px}
.slide-arrow{position:absolute;top:295px;width:34px;height:34px;border-radius:50%;background:var(--white);display:flex;align-items:center;justify-content:center}
.slide-arrow.prev{left:30px}.slide-arrow.next{right:32px}

/* headings */
.sec-title{text-align:center;font-size:30px;font-weight:700;color:var(--blue)}
.sec-title span{color:var(--green)}

/* services */
.services{top:811px;height:451px;background:var(--white)}
.services .sec-title{margin-top:38px}
.service-card{position:absolute;top:109px;width:241px;height:284px;background:var(--card);text-align:center}
.service-icon{width:106px;height:106px;border-radius:50%;border:5px solid var(--green);background:var(--white);margin:12px auto 0;display:flex;align-items:center;justify-content:center}
.service-card h3{font-size:16px;font-weight:600;margin-top:18px;text-transform:uppercase}
.service-card p{font-size:12px;line-height:20px;padding:4px 14px 0;height:68px}
.service-card .btn{width:116px;height:36px;line-height:36px;margin-top:10px;font-size:12px}

/* why adopt */
.why{top:1262px;height:278px}
.why-photo{position:absolute;inset:0;background:linear-gradient(90deg,#2a2b2d,#454443 45%,#333 100%)}
.why .sec-title{position:relative;margin-top:44px}
.why-text{position:relative;width:700px;margin:10px auto 0;text-align:center;color:var(--white);font-size:12px;line-height:21px}
.why-more{position:relative;text-align:center;color:var(--white);font-weight:700;font-size:12px;margin-top:14px}

/* screens */
.screens{top:1540px;height:503px;background:var(--light)}
.screens .sec-title{margin-top:40px}
.phone{position:absolute;background:#111;border-radius:14px;box-shadow:0 4px 10px rgba(0,0,0,.25)}
.phone-screen{position:absolute;left:6%;right:6%;top:11%;bottom:12%;background:var(--white);overflow:hidden;font-size:7px;line-height:1.3;color:#333}
.app-bar{background:var(--blue);color:var(--white);font-weight:700;font-size:8px;padding:7px 6px;display:flex;justify-content:space-between;align-items:center}
.app-bar i{display:flex;gap:4px}
.app-bar i b{width:6px;height:6px;border:1px solid #fff;border-radius:50%}
.note{margin:5px 4px 0;padding:3px 4px 4px;border-bottom:2px solid var(--line);background:#f6f8fc}
.note strong{display:block;color:var(--blue);font-size:7px}
.note em{font-style:normal;color:#777;font-size:6px}
.task{margin:6px 5px 0;padding:4px 5px;border:1px solid #dde3ee;border-bottom:3px solid var(--blue);position:relative}
.task strong{display:block;color:var(--blue);font-size:8px}
.task em{font-style:normal;color:#777;font-size:6.5px;display:block}
.task .tri{position:absolute;right:5px;top:5px;width:0;height:0;border-left:5px solid transparent;border-right:5px solid transparent;border-bottom:8px solid var(--green)}
.task .meta{display:flex;align-items:center;gap:3px;margin-top:3px;color:var(--pin);font-size:8px;font-weight:700}
.menu{background:var(--blue);height:100%;color:var(--white)}
.menu-head{background:var(--white);color:var(--blue);padding:6px;font-size:8px;font-weight:700}
.menu-head b{display:block;width:16px;height:16px;border-radius:50%;background:#f2c23a;margin-bottom:3px}
.menu li{list-style:none;padding:5px 8px;border-bottom:1px solid var(--blue-mid);font-size:6.5px;display:flex;gap:5px;align-items:center}
.menu li::before{content:"";width:5px;height:5px;background:#9fb8e6;border-radius:1px}
.menu li.on{background:var(--blue-mid)}

/* testimonials */
.testimonials{top:2043px;height:297px}
.testi-photo{position:absolute;inset:0;background:linear-gradient(90deg,#353535,#4a4845 50%,#2f2e2d)}
.testimonials .sec-title{position:relative;margin-top:36px;color:var(--green)}
.testi-text{position:relative;width:700px;margin:6px auto 0;text-align:center;color:var(--white);font-size:12px;line-height:21px}
.testi-quote{position:relative;display:block;margin:16px auto 0}
.testi-name{position:relative;text-align:center;color:var(--white);font-weight:700;font-size:11px;margin-top:8px}
.testi-city{position:relative;text-align:center;color:var(--white);font-size:11px;margin-top:2px}

/* join */
.join{top:2340px;height:139px;background:var(--light)}
.join h2{position:absolute;left:88px;top:26px;font-size:25px;font-weight:700;color:var(--blue)}
.join-field{position:absolute;left:88px;top:68px;width:787px;height:43px;background:var(--white);border-radius:3px;font-size:13px;font-style:italic;color:#333;padding:12px 14px}
.join .btn{position:absolute;left:946px;top:68px;width:168px;height:43px;line-height:43px;color:var(--dark)}

/* footer */
.site-footer{top:2479px;height:297px;background:var(--dark);color:var(--white)}
.foot-brand{position:absolute;left:143px;top:40px;display:flex;align-items:center;gap:12px}
.foot-brand .brand-dot{width:54px;height:54px}
.foot-brand .brand-name{font-size:38px}
.foot-tag{position:absolute;left:88px;top:122px;font-size:12px;color:var(--green)}
.foot-about{position:absolute;left:88px;top:146px;width:302px;font-size:11px;line-height:19px;color:#ddd;text-align:justify}
.foot-title{position:absolute;top:32px;font-size:18px;font-weight:700;text-transform:uppercase}
.quick-links{position:absolute;left:432px;top:84px;list-style:none}
.quick-links li{font-size:12px;height:26px;display:flex;align-items:center;gap:10px}
.map{position:absolute;left:612px;top:99px;width:269px;height:170px;background:
  radial-gradient(circle at 70% 40%,rgba(230,180,90,.35),transparent 45%),
  linear-gradient(135deg,#d8d5cc,#ecebe6 50%,#c9d6e4)}
.social{position:absolute;left:939px;top:101px;display:flex;gap:8px}
.social span{width:38px;height:38px;background:#eaeaea;border-radius:3px;display:flex;align-items:center;justify-content:center}
.social span b{width:14px;height:14px;background:#3a3a3a;border-radius:2px}
.contact-line{position:absolute;left:939px;font-size:11px;display:flex;align-items:center;gap:8px}
.copyright{top:2776px;height:41px;background:var(--darker);color:#bbb;font-size:11px;text-align:center;line-height:41px}
</style>
</head>
<body>

<header class="section site-header">
  <div class="brand"><span class="brand-dot"></span><span class="brand-name">RV7</span></div>
  <p class="brand-tag">Rapid Vigil Field Operations Suite</p>
  <div class="login">
    <svg width="11" height="12" viewBox="0 0 11 12"><circle cx="5.5" cy="3" r="3" fill="#222"/><path d="M0 12c0-4 2.5-5.5 5.5-5.5S11 8 11 12z" fill="#222"/></svg>
    LOG IN
  </div>
</header>

<nav class="section main-nav">
  <ul class="nav-list">
    <li class="active">HOME</li>
    <li>ABOUT US</li>
    <li>SERVICES</li>
    <li>TESTIMONIALS</li>
    <li>WEB APPLICATION</li>
    <li>WHY ADOPT RV7</li>
    <li>CONTACT</li>
  </ul>
  <div class="search">
    <div class="search-field">Search..</div>
    <div class="search-btn"><svg width="16" height="16" viewBox="0 0 16 16"><circle cx="6.5" cy="6.5" r="5" stroke="#fff" stroke-width="2" fill="none"/><path d="M10 10l5 5" stroke="#fff" stroke-width="2.4"/></svg></div>
  </div>
</nav>

<section class="section hero">
  <div class="hero-photo" role="img" aria-label="Photo of an office team reviewing charts and documents together"></div>
  <div class="slide-arrow prev"><svg width="14" height="14" viewBox="0 0 14 14"><path d="M9 2L4 7l5 5" stroke="#333" stroke-width="3" fill="none"/></svg></div>
  <div class="slide-arrow next"><svg width="14" height="14" viewBox="0 0 14 14"><path d="M5 2l5 5-5 5" stroke="#333" stroke-width="3" fill="none"/></svg></div>
  <div class="hero-caption">
    <h1>WELCOME TO RV7</h1>
    <p>RV7 offers a web based and mobile interface to assist the CERT Community.</p>
    <span class="btn">Read More</span>
  </div>
</section>

<section class="section services">
  <h2 class="sec-title">OUR <span>SERVICES</span></h2>
  <article class="service-card" style="left:86px">
    <div class="service-icon"><svg width="52" height="52" viewBox="0 0 52 52" fill="var(--blue)"><rect x="18" y="8" width="30" height="22" fill="none" stroke="var(--blue)" stroke-width="3"/><path d="M24 24l6-7 5 4 7-8" stroke="var(--blue)" stroke-width="2.5" fill="none"/><circle cx="11" cy="20" r="5"/><path d="M3 44v-12c0-5 4-7 8-7s8 2 8 7v12z"/></svg></div>
    <h3>Incident Management</h3>
    <p>Log incidents, map damage and follow status from one live board.</p>
    <span class="btn">Read More</span>
  </article>
  <article class="service-card" style="left:349px">
    <div class="service-icon"><svg width="56" height="52" viewBox="0 0 56 52" fill="var(--blue)"><circle cx="16" cy="12" r="5"/><circle cx="40" cy="12" r="5"/><circle cx="28" cy="20" r="5"/><path d="M8 34c0-6 4-9 8-9s8 3 8 9z"/><path d="M32 34c0-6 4-9 8-9s8 3 8 9z"/><rect x="6" y="34" width="44" height="5"/><rect x="10" y="39" width="4" height="10"/><rect x="42" y="39" width="4" height="10"/></svg></div>
    <h3>Team Management</h3>
    <p>Build teams fast, assign roles and see who is on duty now.</p>
    <span class="btn">Read More</span>
  </article>
  <article class="service-card" style="left:612px">
    <div class="service-icon"><svg width="52" height="52" viewBox="0 0 52 52" fill="var(--blue)"><circle cx="16" cy="9" r="5"/><path d="M10 16h12l3 14h-4l-2 18h-6l-2-18h-4z"/><circle cx="36" cy="15" r="5"/><path d="M31 22h10l2 12h-3l-2 14h-4l-2-14h-3z"/><path d="M23 20l8 6" stroke="var(--blue)" stroke-width="3"/></svg></div>
    <h3>Task Management</h3>
    <p>Create tasks, set priority and track progress until every job is done.</p>
    <span class="btn">Read More</span>
  </article>
  <article class="service-card" style="left:875px">
    <div class="service-icon"><svg width="52" height="52" viewBox="0 0 52 52" fill="var(--blue)"><rect x="24" y="6" width="22" height="14" rx="2"/><circle cx="16" cy="18" r="5"/><path d="M8 44V30c0-5 4-7 8-7s8 2 8 7v14z"/><circle cx="36" cy="28" r="5"/><path d="M28 46V38c0-4 4-6 8-6s8 2 8 6v8z"/></svg></div>
    <h3>Communication</h3>
    <p>Send alerts by text, email and app to every volunteer at once.</p>
    <span class="btn">Read More</span>
  </article>
</section>

<section class="section why">
  <div class="why-photo" role="img" aria-label="Dimmed photo of a team working at a table"></div>
  <h2 class="sec-title">WHY <span>ADOPT RV7</span></h2>
  <p class="why-text">Easy system to register volunteers. Accurate identification of number of CERT Volunteers available to help in an incident. Efficient communication mechanism to reach out to the volunteers via SMS. Rich graphical visualization of Incidents &amp; Damages associated with the incidents. Easy management and tracking of resources associated with Capture Notes and pictures about situations being handled. Easy one click notification to teams on the ground and team members on the same task. One click social media integration with major social channels related to the Incident.</p>
  <p class="why-more">READ MORE &gt;&gt;</p>
</section>

<section class="section screens">
  <h2 class="sec-title">VOLUNTEER <span>MOBILE SCREENS</span></h2>

  <div class="phone" style="left:218px;top:154px;width:124px;height:259px"><div class="phone-screen">
    <div class="note"><strong>Weather alert</strong><em>Stay indoors tonight</em></div>
    <div class="note"><strong>Road closed</strong><em>Use north route</em></div>
  </div></div>

  <div class="phone" style="left:353px;top:137px;width:150px;height:299px"><div class="phone-screen">
    <div class="menu">
      <div class="menu-head"><b></b>Volunteer</div>
      <ul>
        <li>Dashboard</li><li class="on">Notifications</li><li>Profile</li><li>Tasks</li><li>Shelters</li><li>Map</li><li>Help</li><li>Logout</li>
      </ul>
    </div>
  </div></div>

  <div class="phone" style="left:516px;top:113px;width:164px;height:343px"><div class="phone-screen">
    <div class="app-bar">TODO List<i><b></b><b></b></i></div>
    <div class="task"><span class="tri" style="border-bottom-color:var(--alert)"></span><strong>Ground task</strong><em>Supply distribution</em><div class="meta"><svg width="7" height="7" viewBox="0 0 7 7"><circle cx="3.5" cy="3.5" r="3" stroke="#d9334f" fill="none"/><path d="M3.5 2v1.8h1.3" stroke="#d9334f" fill="none"/></svg>03 Min</div></div>
    <div class="task"><span class="tri"></span><strong>Find damage area</strong><em>Damage assessment</em><div class="meta"><svg width="7" height="7" viewBox="0 0 7 7"><circle cx="3.5" cy="3.5" r="3" stroke="#d9334f" fill="none"/><path d="M3.5 2v1.8h1.3" stroke="#d9334f" fill="none"/></svg>40 Min</div></div>
    <div class="task"><span class="tri"></span><strong>Supply food</strong><em>Supply distribution</em><div class="meta"><svg width="7" height="7" viewBox="0 0 7 7"><circle cx="3.5" cy="3.5" r="3" stroke="#d9334f" fill="none"/><path d="M3.5 2v1.8h1.3" stroke="#d9334f" fill="none"/></svg>40 Min</div></div>
  </div></div>

  <div class="phone" style="left:695px;top:128px;width:148px;height:309px"><div class="phone-screen">
    <div class="app-bar">Notifications<i><b></b></i></div>
    <div class="note"><strong>Weather alert</strong><em>Stay indoors tonight</em></div>
    <div class="note"><strong>Road closed</strong><em>Use north route</em></div>
  </div></div>

  <div class="phone" style="left:856px;top:154px;width:124px;height:259px"><div class="phone-screen">
    <div class="note"><strong>Weather alert</strong><em>Stay indoors tonight</em></div>
    <div class="note"><strong>Road closed</strong><em>Use north route</em></div>
  </div></div>
</section>

<section class="section testimonials">
  <div class="testi-photo" role="img" aria-label="Dimmed photo of colleagues in a meeting"></div>
  <h2 class="sec-title">TESTIMONIALS</h2>
  <p class="testi-text">Register volunteers. Accurate identification of number of CERT Volunteers available to help in an incident. Efficient communication mechanism to reach out to the volunteers via SMS. Rich graphical visualization of Incidents &amp; Damages associated with the incidents. Easy management and tracking with Capture Notes and pictures.</p>
  <svg class="testi-quote" width="40" height="32" viewBox="0 0 40 32" fill="var(--blue)"><path d="M0 0h17v17l-6 15H4l5-14H0z"/><path d="M22 0h17v17l-6 15h-7l5-14h-9z"/></svg>
  <p class="testi-name">MIRA KESTREL</p>
  <p class="testi-city">HARBOR CITY</p>
</section>

<section class="section join">
  <h2>JOIN WITH US</h2>
  <div class="join-field">E mail address</div>
  <span class="btn">Join Us</span>
</section>

<footer class="section site-footer">
  <div class="foot-brand"><span class="brand-dot"></span><span class="brand-name">RV7</span></div>
  <p class="foot-tag">Rapid Vigil Field Operations Suite</p>
  <p class="foot-about">RV7 offers a web based and mobile interface to assist the CERT Community. The roles from CERT teams have been created to have access to either the web, mobile or both the interfaces. RV7 offers a web based and mobile interface to assist the CERT Community. The roles from CERT teams have been created to have access.</p>

  <h3 class="foot-title" style="left:432px">Quick Links</h3>
  <ul class="quick-links">
    <li><svg width="12" height="8" viewBox="0 0 12 8"><path d="M0 4h10M7 1l3 3-3 3" stroke="#fff" stroke-width="1.5" fill="none"/></svg>Home</li>
    <li><svg width="12" height="8" viewBox="0 0 12 8"><path d="M0 4h10M7 1l3 3-3 3" stroke="#fff" stroke-width="1.5" fill="none"/></svg>About us</li>
    <li><svg width="12" height="8" viewBox="0 0 12 8"><path d="M0 4h10M7 1l3 3-3 3" stroke="#fff" stroke-width="1.5" fill="none"/></svg>Services</li>
    <li><svg width="12" height="8" viewBox="0 0 12 8"><path d="M0 4h10M7 1l3 3-3 3" stroke="#fff" stroke-width="1.5" fill="none"/></svg>Testimonials</li>
    <li><svg width="12" height="8" viewBox="0 0 12 8"><path d="M0 4h10M7 1l3 3-3 3" stroke="#fff" stroke-width="1.5" fill="none"/></svg>Web application</li>
    <li><svg width="12" height="8" viewBox="0 0 12 8"><path d="M0 4h10M7 1l3 3-3 3" stroke="#fff" stroke-width="1.5" fill="none"/></svg>Why adopt RV7</li>
    <li><svg width="12" height="8" viewBox="0 0 12 8"><path d="M0 4h10M7 1l3 3-3 3" stroke="#fff" stroke-width="1.5" fill="none"/></svg>Contact</li>
  </ul>

  <h3 class="foot-title" style="left:612px">Location</h3>
  <div class="map" role="img" aria-label="Street map showing the office location"></div>

  <h3 class="foot-title" style="left:939px">Follow Us</h3>
  <div class="social"><span><b></b></span><span><b></b></span><span><b></b></span><span><b></b></span></div>
  <p class="contact-line" style="top:165px"><svg width="11" height="11" viewBox="0 0 11 11"><path d="M2 0l2 2.5-1 1.5c.8 1.6 2 2.8 3.5 3.5l1.5-1L11 8.5 9.5 11C4 10.5.5 7 0 1.5z" fill="#fff"/></svg>555-014-2290</p>
  <p class="contact-line" style="top:189px"><svg width="12" height="9" viewBox="0 0 12 9"><rect width="12" height="9" fill="#fff"/><path d="M0 0l6 5 6-5" stroke="#2a2a2a" fill="none"/></svg>mira.kestrel@example.com</p>
</footer>

<div class="section copyright">@copyright 2016 RV7.All Rights Reserved</div>

</body>
</html>
```